DESKHAVEN COSPACE Website design and coding

DESKHAVEN COSPACE

DESKHAVEN is Galveston’s first (and currently only) shared business co-working space. We share the same upscale, casual work environment, but we work independently on our own (or our team’s) projects and goals. For only a flat $195 membership fee per month, you have your very own all-inclusive, fun, personal business office environment. Website is written (Word file #12, below); and all pictures etc provided. Galveston is a beachy, coastal, historic city an hour from Houston, Texas USA. Logo (file 11 below) is temporary only.

Target Market(s)

Outside sales people, medical students looking for study hall, Houston companies looking for local office, real estate agents, graphic artists, entrepreneurs, etc

Contact Information for Business Card

will discuss --want to combine with current business card with multiple businesses

Logo Text

DESKHAVEN COSPACE

Coding

Coded - Design and coding required

Number of Pages Required

5+ page

Colors
ec1f27
fbed22

Requirements
Nice to have
• maroon/wine dominant with yellow and red accents, gray base are the colors of the space--website could coordinate--but open to creative ideas/combinations

```html
<!DOCTYPE html>
<html lang="en">
<head>
<meta charset="utf-8">
<title>Deskhaven Cospace – Contact</title>
<link href="https://fonts.googleapis.com/css2?family=Montserrat:wght@500;600;700;800&family=Open+Sans:wght@400&display=swap" rel="stylesheet">
<style>
:root{
  --red:#cf0a17;
  --yellow:#f9ec22;
  --ink:#111111;
  --gray:#6b6b6b;
  --line:#dcdcdc;
  --white:#ffffff;
}
*{box-sizing:border-box;margin:0;padding:0}
html,body{width:1200px;height:1191px;overflow:hidden;background:var(--white)}
body{position:relative;font-family:'Montserrat',sans-serif;color:var(--ink)}
.abs{position:absolute}
.site-header{position:absolute;left:0;top:0;width:1200px;height:76px;background:var(--white)}
.brand{position:absolute;font-family:'Montserrat',sans-serif;font-weight:800;font-size:27px;letter-spacing:-0.5px;line-height:1}
.site-header .brand{left:135px;top:21px;color:var(--gray)}
.nav{position:absolute;top:0;left:0;width:1200px;font-weight:600;font-size:12.5px;letter-spacing:0.2px}
.nav a{position:absolute;color:var(--ink);text-decoration:none;white-space:nowrap}
.site-header .nav a{top:27px}
.nav a.current{color:var(--red)}
.hero{position:absolute;left:0;top:76px;width:1200px;height:498px;
  background:linear-gradient(180deg,#cfc9bd 0%,#bfb7a6 30%,#7d7468 58%,#3e3a37 85%,#2c2a29 100%)}
.contact-panel{position:absolute;left:134px;top:452px;width:445px;height:378px;background:var(--red);color:var(--white)}
.contact-panel h1{position:absolute;left:33px;top:25px;font-size:27px;font-weight:700;letter-spacing:0.3px}
.contact-row{position:absolute;left:38px;font-size:13px;font-weight:700;white-space:nowrap}
.contact-row .val{position:absolute;left:126px}
.contact-row .cont{position:absolute;left:133px}
.form-card{position:absolute;left:618px;top:452px;width:444px;height:523px;background:var(--white);box-shadow:0 4px 22px rgba(0,0,0,0.10)}
.form-card h2{position:absolute;left:26px;top:24px;font-size:15.5px;font-weight:600}
.field-label{position:absolute;font-family:'Open Sans',sans-serif;font-size:12px;color:#333}
.field{position:absolute;border:1px solid var(--line);background:var(--white)}
.submit{position:absolute;left:275px;top:441px;width:140px;height:43px;background:var(--red);color:var(--white);
  font-size:11.5px;font-weight:700;display:flex;align-items:center;justify-content:center;border:none}
.site-footer{position:absolute;left:0;top:1046px;width:1200px;height:115px;background:var(--red);color:var(--white)}
.site-footer .brand{left:135px;top:18px;color:var(--white)}
.site-footer .nav a{top:31px;color:var(--white)}
.footer-address{position:absolute;left:136px;top:58px;font-size:13px;font-weight:500;line-height:15px}
.copyright-bar{position:absolute;left:0;top:1161px;width:1200px;height:28px;background:var(--yellow);border-bottom:2px solid var(--red)}
.copyright-bar p{position:absolute;left:136px;top:8px;font-size:11px;font-weight:700}
</style>
</head>
<body>
<header class="site-header">
  <div class="brand">DESKHAVEN</div>
  <nav class="nav">
    <a style="left:423px">ABOUT</a>
    <a style="left:488px">AMENITIES</a>
    <a style="left:583px">MEMBERSHIP</a>
    <a style="left:701px">PICTURES</a>
    <a style="left:792px">THE DESKHAVEN PILOSOPHY</a>
    <a class="current" style="left:997px">CONTACT</a>
  </nav>
</header>

<div class="hero" role="img" aria-label="Photo of the co-working lounge with a wooden bar table, red lockers, black and white sofas and yellow office chairs"></div>

<section class="contact-panel">
  <h1>CONTACT</h1>
  <div class="contact-row" style="top:91px">Email<span class="val">: hello@deskhavencospace.com</span></div>
  <div class="contact-row" style="top:117px">Phone<span class="val">:</span></div>
  <div class="contact-row" style="top:144px">Facebook<span class="val">:</span></div>
  <div class="contact-row" style="top:170px">Linked In<span class="val">:</span></div>
  <div class="contact-row" style="top:196px">Instagram<span class="val">:</span></div>
  <div class="contact-row" style="top:223px">Physical location<span class="val">: Deskhaven Cospace</span></div>
  <div class="contact-row" style="top:250px"><span class="cont">418 Harbor Ave, Suite 204</span></div>
  <div class="contact-row" style="top:276px"><span class="cont">Galveston, TX 77550</span></div>
  <div class="contact-row" style="top:302px">Owner<span class="val">: Lindqvist Holdings</span></div>
  <div class="contact-row" style="top:329px"><span class="cont">mara@lindqvistholdings.com</span></div>
  <div class="contact-row" style="top:355px"><span class="cont">713-555-0148</span></div>
</section>

<section class="form-card">
  <h2>Mailing address for management:</h2>
  <label class="field-label" style="left:25px;top:64px">First Name</label>
  <div class="field" style="left:25px;top:80px;width:183px;height:40px"></div>
  <label class="field-label" style="left:233px;top:64px">Last Name</label>
  <div class="field" style="left:235px;top:80px;width:182px;height:40px"></div>
  <label class="field-label" style="left:25px;top:125px">Email</label>
  <div class="field" style="left:25px;top:142px;width:392px;height:39px"></div>
  <label class="field-label" style="left:25px;top:187px">Phone</label>
  <div class="field" style="left:25px;top:203px;width:392px;height:40px"></div>
  <label class="field-label" style="left:25px;top:252px">Address</label>
  <div class="field" style="left:25px;top:269px;width:392px;height:40px"></div>
  <label class="field-label" style="left:25px;top:316px">Description</label>
  <div class="field" style="left:25px;top:332px;width:390px;height:89px"></div>
  <button class="submit">SUBMIT</button>
</section>

<footer class="site-footer">
  <div class="brand">DESKHAVEN</div>
  <div class="footer-address">Deskhaven Cospace<br>418 Harbor Ave, Suite 204<br>Galveston, TX 77550</div>
  <nav class="nav">
    <a style="left:424px">ABOUT</a>
    <a style="left:489px">AMENITIES</a>
    <a style="left:584px">MEMBERSHIP</a>
    <a style="left:702px">PICTURES</a>
    <a style="left:793px">THE DESKHAVEN PILOSOPHY</a>
    <a style="left:998px">CONTACT</a>
  </nav>
</footer>
<div class="copyright-bar"><p>Copyright 2020 DESKHAVEN COSPACE</p></div>
</body>
</html>
```